I would like a single page website for Skyward Rentals Pacific. In the file list provided there is basic information to be included as well as our logo with colors, fonts and images to be included.
Site must be very simple and be able to be loaded onto smart phones etc very quickly.
Site needs to be very smart in appearance

Target Market(s)

All prospective drone customers from Police to Parties.

Industry/Entity Type

Hire

Requirements
Must have
• Must have variation of color schemes supplied
Nice to have
• Must be very eye catching without going over the top
Should not have
• Anything slow to load.

```html
<!DOCTYPE html>
<html lang="en">
<head>
<meta charset="utf-8">
<title>Skyward Rentals Pacific</title>
<link rel="stylesheet" href="https://fonts.googleapis.com/css2?family=Barlow:wght@400;500&family=Open+Sans:wght@400&family=Raleway:wght@400;500&display=swap">
<style>
:root{
  --navy:#151e7a;
  --ink:#2a2a2a;
  --grey:#6f6f6f;
  --nav-grey:#8a8a8a;
  --hero-a:#2c3cb0;
  --hero-b:#4a5cd3;
  --rule:#d6d6d6;
  --footer:#222222;
  --footer-deep:#171717;
  --footer-text:#a9a9a9;
  --accent:#5cb2e6;
  --field:#3a3a3a;
  --field-btn:#4c4c4c;
}
*{margin:0;padding:0;box-sizing:border-box}
html,body{width:1187px;height:1200px;overflow:hidden;background:#fff}
body{position:relative;font-family:"Barlow",sans-serif;color:var(--ink)}
.abs{position:absolute}

/* header */
.brand{left:98px;top:30px;display:flex;align-items:center;gap:10px}
.brand-dot{width:22px;height:22px;border-radius:50%;background:var(--navy)}
.brand-name{font-family:"Barlow",sans-serif;font-weight:500;font-size:26px;color:var(--navy);letter-spacing:.3px;line-height:1}
.callout{right:99px;top:24px;font-family:"Raleway",sans-serif;font-size:16px;color:var(--nav-grey)}
.callout strong{font-weight:500;color:var(--navy);font-size:17px}
.main-nav{right:99px;top:69px;display:flex;gap:43px;font-family:"Barlow",sans-serif;font-size:13px;letter-spacing:.6px;color:var(--nav-grey)}
.main-nav .current{color:var(--navy)}

/* hero */
.hero{left:97px;top:108px;width:992px;height:373px;background:linear-gradient(120deg,var(--hero-a) 0%,#3a4cc4 55%,var(--hero-b) 100%);overflow:hidden}
.hero-visual{position:absolute;left:136px;top:53px;width:437px;height:229px;border-radius:40px;background:radial-gradient(ellipse at center,#e9ecf5 0%,#c9cfe6 45%,rgba(90,105,210,0) 72%)}
.hero-copy{position:absolute;right:91px;top:114px;text-align:right;color:#fff;font-weight:500;font-size:31px;line-height:36px}
.hero-cta{position:absolute;left:804px;top:201px;width:97px;height:37px;background:#fff;border-radius:2px;color:var(--navy);font-size:15px;font-weight:500;display:flex;align-items:center;justify-content:center}
.hero-arrow{position:absolute;top:169px;width:26px;height:34px;background:rgba(20,30,110,.45);display:flex;align-items:center;justify-content:center}
.hero-arrow.prev{left:0}
.hero-arrow.next{right:0}

/* intro */
.intro{left:97px;top:525px;width:992px;text-align:center;font-size:15.5px;line-height:24px;color:var(--grey)}
.divider{left:97px;top:614px;width:992px;height:1px;background:var(--rule)}

/* services */
.services-head{left:0;top:645px;width:1187px;display:flex;justify-content:center;align-items:center;gap:22px}
.services-title{font-size:21px;font-weight:500;color:var(--navy)}
.service-card{top:695px;width:185px;text-align:center}
.service-photo{width:185px;height:129px}
.service-caption{margin-top:10px;font-size:13.5px;line-height:19px;color:var(--ink);font-weight:500}

/* footer */
.footer{left:0;top:915px;width:1187px;height:197px;background:var(--footer)}
.footer-base{left:0;top:1112px;width:1187px;height:88px;background:var(--footer-deep)}
.footer-heading{font-family:"Barlow",sans-serif;font-weight:500;font-size:18px;color:var(--accent);letter-spacing:.3px}
.signup{left:116px;top:979px;width:247px;height:35px;background:var(--field);display:flex}
.signup-field{flex:1;padding-left:14px;display:flex;align-items:center;font-family:"Open Sans",sans-serif;font-size:11px;color:#c8c8c8}
.signup-btn{width:32px;background:var(--field-btn);display:flex;align-items:center;justify-content:center}
.socials{left:123px;top:1042px;display:flex;gap:6px}
.social{width:28px;height:28px;border-radius:50%}
.footer-split{left:410px;top:946px;width:1px;height:135px;background:#3c3c3c}
.link-list{list-style:none;font-family:"Open Sans",sans-serif;font-size:11px;color:var(--footer-text)}
.link-list li{position:relative;padding-left:10px;line-height:15px}
.link-list li::before{content:"";position:absolute;left:0;top:7px;width:3px;height:3px;border-radius:50%;background:#7a7a7a}
.contact-list li{margin-bottom:14px}
.cat-list li{margin-bottom:5.3px}
.base-nav{left:0;top:1133px;width:1187px;text-align:center;font-family:"Open Sans",sans-serif;font-size:11.5px;color:var(--footer-text)}
.base-nav span.sep{margin:0 10px;color:#666}
.copyright{left:0;top:1161px;width:1187px;text-align:center;font-family:"Open Sans",sans-serif;font-size:11.5px;color:var(--footer-text)}
</style>
</head>
<body>

<header>
  <div class="abs brand"><span class="brand-dot"></span><span class="brand-name">Skyward Rentals Pacific</span></div>
  <div class="abs callout">Call us on : <strong>0400 555 019</strong></div>
  <nav class="abs main-nav">
    <span class="current">HOME</span><span>ABOUT US</span><span>SERVICES</span><span>CONTACT US</span>
  </nav>
</header>

<section class="abs hero">
  <div class="hero-visual" role="img" aria-label="White quadcopter drone with camera gimbal in flight"></div>
  <div class="hero-copy">4K Video Footage,<br>12mp Images</div>
  <div class="hero-cta">Book now</div>
  <div class="hero-arrow prev"><svg width="10" height="18" viewBox="0 0 10 18"><path d="M9 1 1 9l8 8" fill="none" stroke="#c9d0f5" stroke-width="1.3"/></svg></div>
  <div class="hero-arrow next"><svg width="10" height="18" viewBox="0 0 10 18"><path d="M1 1l8 8-8 8" fill="none" stroke="#c9d0f5" stroke-width="1.3"/></svg></div>
</section>

<p class="abs intro">ASRA certified company and ASRA endorsed pilot, with Full Public Liability Insurance. All operating licences are in place and are carried on the operator. All drones are maintained to full ASRA compliance standards</p>
<div class="abs divider"></div>

<div class="abs services-head">
  <svg width="10" height="16" viewBox="0 0 10 16"><path d="M8 2 2 8l6 6" fill="none" stroke="#8a8a8a" stroke-width="2.4"/></svg>
  <span class="services-title">We Do Service For...</span>
  <svg width="10" height="16" viewBox="0 0 10 16"><path d="M2 2l6 6-6 6" fill="none" stroke="#8a8a8a" stroke-width="2.4"/></svg>
</div>

<div class="abs service-card" style="left:98px">
  <div class="service-photo" role="img" aria-label="Children at a colourful birthday party table" style="background:linear-gradient(160deg,#b8a27a,#c9423e 45%,#3f8ec0 75%,#5a4a3a)"></div>
  <p class="service-caption">Special Occasions, Childrenis<br>Birthday Parties, Weddings</p>
</div>
<div class="abs service-card" style="left:299px">
  <div class="service-photo" role="img" aria-label="Marathon runners passing historic city buildings" style="background:linear-gradient(180deg,#dcd8cf 0%,#a08a66 40%,#8c8a86 70%,#b8b6b0)"></div>
  <p class="service-caption">Sporting events</p>
</div>
<div class="abs service-card" style="left:501px">
  <div class="service-photo" role="img" aria-label="Aerial view of a coastal town with parked cars" style="background:linear-gradient(180deg,#6d99c4 0%,#b19a86 35%,#5f6468 70%,#3c4146)"></div>
  <p class="service-caption">Real Estate Brochures</p>
</div>
<div class="abs service-card" style="left:702px">
  <div class="service-photo" role="img" aria-label="Aerial view of a construction site with cranes" style="background:linear-gradient(180deg,#8fb6de 0%,#8a8b84 40%,#6f6a5e 70%,#7d8a6a)"></div>
  <p class="service-caption">Construction project updates<br>for remote stake holders</p>
</div>
<div class="abs service-card" style="left:903px">
  <div class="service-photo" role="img" aria-label="Green surveillance display with drone outline" style="background:radial-gradient(circle at 50% 50%,#6fa567,#2f5f2c 70%,#1e3d1c)"></div>
  <p class="service-caption">Surveillance Police, Local<br>councilsworksafeetc</p>
</div>

<footer>
  <div class="abs footer"></div>
  <h3 class="abs footer-heading" style="left:115px;top:949px">NEWSLETTER SIGNUP</h3>
  <div class="abs signup">
    <div class="signup-field">Enter E-mail ID</div>
    <div class="signup-btn"><svg width="10" height="16" viewBox="0 0 10 16"><path d="M2 2l6 6-6 6" fill="none" stroke="#fff" stroke-width="1.8"/></svg></div>
  </div>
  <div class="abs socials">
    <span class="social" style="background:#3b5a9a"></span>
    <span class="social" style="background:#2aa3e0"></span>
    <span class="social" style="background:#333"></span>
    <span class="social" style="background:#f26b1d"></span>
    <span class="social" style="background:#e2262a"></span>
    <span class="social" style="background:#4b7bb0"></span>
    <span class="social" style="background:#4aa03a"></span>
  </div>
  <div class="abs footer-split"></div>

  <h3 class="abs footer-heading" style="left:463px;top:949px">QUICK LINKS</h3>
  <ul class="abs link-list contact-list" style="left:463px;top:984px">
    <li>55 Building name, Street name<br>City - Zipcode</li>
    <li>Phone : 0400 555 019</li>
    <li>E-mail : info@skywardrentalspacific.com</li>
  </ul>
  <ul class="abs link-list cat-list" style="left:751px;top:984px">
    <li>Parties</li><li>Sporting events</li><li>Real Estate Brochures</li><li>Construction</li><li>Surveillance</li>
  </ul>
  <ul class="abs link-list cat-list" style="left:938px;top:984px">
    <li>Building Condition</li><li>Lost pets</li><li>Accident reconstructions</li><li>Insurance assessing</li>
  </ul>

  <div class="abs footer-base"></div>
  <nav class="abs base-nav">Home<span class="sep">|</span>About us<span class="sep">|</span>Services<span class="sep">|</span>Contact us</nav>
  <p class="abs copyright">Copyright &copy; 2015 Skyward Rentals Pacific.&nbsp;&nbsp; All rights reserved.</p>
</footer>

</body>
</html>
```